Business Card Design for Occupational Medicine Start Up Company

We need to design a professional business card. We are a healthcare company providing occupational medicine services to blue collar industries. We are professional, efficient and high quality service providers.

Target Market(s)

Blue Collar Industry: Shipbuilding, Ports, Trucking Companies; The Executives and Safety Officers for these companies

Industry/Entity Type

Healthcare

Contact Information for Business Card

Logo, Name, Title, Email, Phone

Other font styles liked:
• Please match our Brand Guide

Requirements
Must have
• Our Company Colors and Logo

```html
<!DOCTYPE html>
<html lang="en">
<head>
<meta charset="utf-8">
<title>CrewCare Clinics – Business Card</title>
<link rel="stylesheet" href="https://fonts.googleapis.com/css2?family=Montserrat:wght@400;500;700;800&display=swap">
<style>
  :root {
    --navy: #2a2a7a;
    --card-back: #2c2a82;
    --pattern-light: #5350a8;
    --ink: #222230;
    --paper: #ffffff;
    --stage: #2b2b2d;
    --gold: #f0b23c;
  }
  * { box-sizing: border-box; margin: 0; padding: 0; }
  html, body { width: 1200px; height: 1200px; overflow: hidden; }
  body {
    background: var(--stage);
    font-family: "Montserrat", sans-serif;
    display: flex;
    align-items: center;
    justify-content: center;
    gap: 80px;
  }
  .card {
    width: 420px;
    height: 720px;
    border-radius: 28px;
    position: relative;
    overflow: hidden;
  }
  /* Front */
  .card-front {
    background: var(--paper);
    color: var(--ink);
    display: flex;
    flex-direction: column;
    align-items: center;
    padding-top: 120px;
  }
  .brand {
    display: flex;
    align-items: center;
    gap: 12px;
    color: var(--navy);
    font-weight: 800;
    font-size: 30px;
    letter-spacing: 0.5px;
  }
  .brand-dot {
    width: 30px; height: 30px;
    border-radius: 50%;
    background: var(--navy);
    flex: none;
  }
  .holder { margin-top: 90px; text-align: center; }
  .holder-name { color: var(--navy); font-weight: 700; font-size: 24px; }
  .holder-title { font-size: 15px; margin-top: 4px; }
  .divider-icons {
    display: flex; align-items: center; gap: 10px;
    margin-top: 24px; width: 300px;
  }
  .divider-icons .rule { flex: 1; height: 2px; background: var(--navy); }
  .icon {
    width: 22px; height: 22px; border-radius: 5px;
    background: var(--navy);
    display: flex; align-items: center; justify-content: center;
  }
  .contact { margin-top: 22px; text-align: center; font-size: 16px; line-height: 1.5; }
  .short-rule { width: 100px; height: 2px; background: var(--navy); margin: 22px 0; }
  .address { text-align: center; font-size: 16px; line-height: 1.5; }
  /* Back */
  .card-back { background: var(--card-back); }
  .back-pattern {
    position: absolute; inset: 0 0 200px 0;
    background: linear-gradient(180deg, var(--pattern-light) 0%, rgba(83,80,168,0.45) 55%, var(--card-back) 100%);
  }
  .back-brand {
    position: absolute; left: 0; right: 0; bottom: 110px;
    display: flex; justify-content: center; align-items: center; gap: 12px;
    color: var(--paper); font-weight: 800; font-size: 30px; letter-spacing: 0.5px;
  }
  .back-brand .brand-dot { background: var(--paper); }
</style>
</head>
<body>
  <section class="card card-front">
    <div class="brand"><span class="brand-dot"></span>CREWCARE CLINICS</div>
    <div class="holder">
      <p class="holder-name">Daniel Reyes</p>
      <p class="holder-title">CEO &amp; Founder</p>
    </div>
    <div class="divider-icons">
      <span class="rule"></span>
      <span class="icon">
        <svg width="14" height="14" viewBox="0 0 24 24"><path fill="#fff" d="M6.6 10.8a15 15 0 0 0 6.6 6.6l2.2-2.2c.3-.3.7-.4 1-.2 1.1.4 2.3.6 3.6.6.6 0 1 .4 1 1V20c0 .6-.4 1-1 1A17 17 0 0 1 3 4c0-.6.4-1 1-1h3.5c.6 0 1 .4 1 1 0 1.3.2 2.5.6 3.6.1.3 0 .7-.2 1z"/></svg>
      </span>
      <span class="icon">
        <svg width="14" height="14" viewBox="0 0 24 24"><rect x="3" y="6" width="18" height="12" rx="1.5" fill="#fff"/><path d="M3.5 7l8.5 6 8.5-6" stroke="#2a2a7a" stroke-width="1.6" fill="none"/></svg>
      </span>
      <span class="icon">
        <svg width="14" height="14" viewBox="0 0 24 24" fill="none" stroke="#fff" stroke-width="2"><circle cx="12" cy="12" r="9"/><path d="M3 12h18M12 3c3 3 3 15 0 18M12 3c-3 3-3 15 0 18"/></svg>
      </span>
      <span class="rule"></span>
    </div>
    <div class="contact">
      <p>800-555-0142</p>
      <p>info@crewcareclinics.com</p>
      <p>www.crewcareclinics.com</p>
    </div>
    <span class="short-rule"></span>
    <div class="address">
      <p>418 Harbor View Rd, #112</p>
      <p>Fairport, OH 44077</p>
    </div>
  </section>

  <section class="card card-back">
    <div class="back-pattern" role="img" aria-label="Repeating brand symbol pattern fading into the card colour"></div>
    <div class="back-brand"><span class="brand-dot"></span>CREWCARE CLINICS</div>
  </section>
</body>
</html>
```